Business Card design for law firm = Brightvale Australia

We are seeking a new design for our business cards.
We are keeping our logo, which is attached.
We need space for
Name
Title
Address is , which is
Level 7
214 Marlowe Street
Sydney NSW 2047
Phone :
Mobile :
Fax :
Email :
DX :
website www.brightvale-example.com.au

Industry/Entity Type

Law Firm / Banking and Finance

Contact Information for Business Card

We are seeking a new design for our business cards. We are keeping our logo. We need space for Name Title Address is Level 7 214 Marlowe Street Sydney NSW 2047 Phone Mobile Fax Email DX website www.brightvale-example.com.au

Colors
0054AA
0677BA
7BADD7
CADEEF
E8F1F8

Requirements
Must have
• see our website for general feel www.brightvale-example.com.au

```html
<!DOCTYPE html>
<html lang="en">
<head>
<meta charset="utf-8">
<title>Brightvale Australia – Business Card</title>
<link rel="stylesheet" href="https://fonts.googleapis.com/css2?family=Nunito+Sans:wght@400;700&display=swap">
<style>
  :root {
    --backdrop: #ababab;
    --navy: #042f5a;
    --teal: #1a93bd;
    --brand-blue: #1458a0;
    --ink: #444a50;
    --paper: #ffffff;
    --sans: "Nunito Sans", Helvetica, Arial, sans-serif;
  }
  * { margin: 0; padding: 0; box-sizing: border-box; }
  html, body { width: 1200px; height: 1000px; overflow: hidden; }
  body { background: var(--backdrop); position: relative; font-family: var(--sans); }

  .card { position: absolute; left: 343px; width: 514px; height: 297px; }

  .card-front { top: 204px; background: var(--navy); }
  .front-name {
    position: absolute; right: 32px; top: 226px;
    font-size: 28px; line-height: 1; font-weight: 400;
    color: var(--teal); letter-spacing: 0.5px;
  }

  .card-back { top: 528px; background: var(--paper); }

  .brand-block { position: absolute; left: 45px; top: 132px; width: 200px; }
  .brand-dot {
    position: absolute; left: 0; top: 8px;
    width: 14px; height: 14px; border-radius: 50%; background: var(--teal);
  }
  .brand-name {
    position: absolute; left: 24px; top: 0;
    font-size: 26px; line-height: 30px; font-weight: 400;
    color: var(--brand-blue); white-space: nowrap; letter-spacing: 0.3px;
  }
  .brand-tagline {
    position: absolute; left: 24px; top: 38px;
    font-size: 12px; color: var(--teal); letter-spacing: 0.4px; white-space: nowrap;
  }

  .contact { position: absolute; right: 32px; top: 66px; text-align: right; white-space: nowrap; }
  .person-name { font-size: 17px; font-weight: 700; color: var(--brand-blue); line-height: 22px; letter-spacing: 0.3px; }
  .person-title { font-size: 12px; color: var(--teal); line-height: 15px; letter-spacing: 0.3px; }
  .address, .numbers { font-size: 12px; color: var(--ink); line-height: 14.5px; letter-spacing: 0.1px; }
  .address { margin-top: 26px; }
  .numbers { margin-top: 14px; }
  .label { font-weight: 700; }
  .website { margin-top: 14px; font-size: 12px; font-weight: 700; color: var(--brand-blue); letter-spacing: 0.1px; }
</style>
</head>
<body>
  <section class="card card-front" aria-label="Card front">
    <div class="front-name">Brightvale</div>
  </section>

  <section class="card card-back" aria-label="Card back">
    <div class="brand-block">
      <div class="brand-dot"></div>
      <div class="brand-name">Brightvale</div>
      <div class="brand-tagline">banking &amp; finance law</div>
    </div>

    <div class="contact">
      <div class="person-name">Helena Marsh</div>
      <div class="person-title">Chief Legal Officer</div>
      <div class="address">
        Level 7, 214 Marlowe Street<br>
        Sydney NSW 2047, <span class="label">DX:</span> 318 Sydney
      </div>
      <div class="numbers">
        <span class="label">P:</span> 02 9000 0142<br>
        <span class="label">F:</span> 02 9000 0175<br>
        <span class="label">E:</span> enquiries@brightvale-example.com.au
      </div>
      <div class="website">www.brightvale-example.com.au</div>
    </div>
  </section>
</body>
</html>
```